Salon and Spa Distributor Business Card

Need a business card. We are are distributor in the salon and spa industry. We identify with natural beauty. Need a card with:
Company Name: Petal Quarry"
Title: "President & CEO"
Address
Company Phone number
email
website
Tag Line:" The Professional Salon Source"

Industry/Entity Type

Business

Contact Information for Business Card

Name: Dov Strommen
Title: "President & CEO"
Address: 31 Harlow Ln, Bexmoor, NJ 07813
Company Phone number: 800-463-5918
email: dovstrommen@petalquarry.example
website: www.petalquarry.example

Requirements
Should not have
• No black backgrounds

```html
<!DOCTYPE html>
<html lang="en">
<head>
<meta charset="utf-8">
<title>Petal Quarry Business Card</title>
<link rel="stylesheet" href="https://fonts.googleapis.com/css2?family=Questrial&family=Arimo:wght@400;700&display=swap">
<style>
  :root {
    --backdrop: #e6e6e6;
    --green-deep: #005b29;
    --green-soft: #3b7f40;
    --green-brand: #3a9a3a;
    --green-name: #1f6b2a;
    --paper: #f7f7f7;
    --paper-edge: #ececec;
    --ink: #333333;
    --ink-soft: #444444;
    --white: #ffffff;
  }
  * { margin: 0; padding: 0; box-sizing: border-box; }
  html, body { width: 1200px; height: 576px; overflow: hidden; }
  body { background: var(--backdrop); position: relative; font-family: "Arimo", sans-serif; }

  .card {
    position: absolute;
    top: 138px;
    width: 484px;
    height: 293px;
    border-radius: 14px;
    box-shadow: 0 3px 8px rgba(0,0,0,0.22);
    overflow: hidden;
  }

  /* Front */
  .card-front {
    left: 82px;
    background: linear-gradient(180deg, var(--green-deep) 0%, var(--green-soft) 100%);
  }
  .front-mark {
    position: absolute;
    left: 0; right: 0;
    top: 80px;
    display: flex;
    flex-direction: column;
    align-items: center;
    gap: 28px;
  }
  .front-mark .brand-dot {
    width: 80px; height: 80px;
    border-radius: 50%;
    background: var(--white);
  }
  .front-mark .wordmark {
    font-family: "Questrial", sans-serif;
    font-size: 29px;
    line-height: 33px;
    color: var(--white);
  }

  /* Back */
  .card-back {
    left: 602px;
    background: linear-gradient(135deg, var(--paper) 0%, var(--paper-edge) 100%);
  }
  .back-deco {
    position: absolute;
    left: 300px; top: 30px;
    width: 210px; height: 210px;
    border-radius: 50%;
    background: rgba(0,0,0,0.03);
  }
  .brand-lockup {
    position: absolute;
    left: 10px; top: 42px;
    display: flex;
    align-items: center;
    gap: 19px;
  }
  .brand-lockup .brand-dot {
    width: 76px; height: 76px;
    border-radius: 50%;
    background: var(--green-brand);
  }
  .brand-lockup .wordmark {
    font-family: "Questrial", sans-serif;
    font-size: 26px;
    color: var(--green-brand);
    line-height: 1;
  }
  .brand-lockup .tagline {
    font-size: 12px;
    color: var(--ink-soft);
    margin-top: 7px;
    margin-left: 3px;
  }

  .holder {
    position: absolute;
    left: 29px; top: 226px;
  }
  .holder .holder-name {
    font-size: 18px;
    line-height: 22px;
    font-weight: 700;
    color: var(--green-name);
  }
  .holder .holder-title {
    font-size: 10px;
    color: var(--ink-soft);
    margin-top: 3px;
  }

  .contact {
    position: absolute;
    left: 232px; top: 185px;
    list-style: none;
    font-size: 12.5px;
    color: var(--ink);
  }
  .contact li {
    display: flex;
    align-items: center;
    gap: 12px;
    height: 18px;
    white-space: nowrap;
  }
  .contact svg { width: 11px; height: 11px; fill: var(--green-name); flex: none; }
  .contact .address { margin-top: 5px; }
</style>
</head>
<body>
  <section class="card card-front">
    <div class="front-mark">
      <span class="brand-dot"></span>
      <span class="wordmark">PetalQuarry</span>
    </div>
  </section>

  <section class="card card-back">
    <div class="back-deco"></div>
    <div class="brand-lockup">
      <span class="brand-dot"></span>
      <div>
        <div class="wordmark">PetalQuarry</div>
        <div class="tagline">The Professional Salon Source</div>
      </div>
    </div>

    <div class="holder">
      <div class="holder-name">Dov Strommen</div>
      <div class="holder-title">President &amp; CEO</div>
    </div>

    <ul class="contact">
      <li>
        <svg viewBox="0 0 12 12" aria-hidden="true"><path d="M1 3 Q6 0 11 3 L10 5 L8 4.5 L8 3.5 Q6 3 4 3.5 L4 4.5 L2 5 Z M3 6 H9 L10 11 H2 Z"/></svg>
        <span>800-463-5918</span>
      </li>
      <li>
        <svg viewBox="0 0 12 12" aria-hidden="true"><path d="M0.5 2.5 H11.5 V9.5 H0.5 Z M1.5 3.5 L6 7 L10.5 3.5 Z" fill-rule="evenodd"/></svg>
        <span>dovstrommen@petalquarry.example</span>
      </li>
      <li>
        <svg viewBox="0 0 12 12" aria-hidden="true"><circle cx="6" cy="6" r="5.5"/><path d="M0.5 6 H11.5 M6 0.5 V11.5" stroke="#f2f2f2" stroke-width="0.9"/><ellipse cx="6" cy="6" rx="2.4" ry="5.5" fill="none" stroke="#f2f2f2" stroke-width="0.9"/></svg>
        <span>www.petalquarry.example</span>
      </li>
      <li class="address">31 Harlow Ln, Bexmoor, NJ 07813</li>
    </ul>
  </section>
</body>
</html>
```